Accountant services flyer & marketing portfolio

I require a design for a marketing portfolio of blank templates for a flyer, product brochure, report cover for A4 based on our style - current logo, letterhead, website look and feel - that can be updated in publisher or word with relevant marketing and company information editorial material and text. It will be either printed A4 or saved as PDF and distributed

Target Market(s)

small business and investment / superfund clients

Industry/Entity Type

Accountant

Font styles to use
Sans Serif

Requirements
Must have
• Instyle of letterhead and website
Professional body logos
Space to input text
Relevant happy images
Nice to have
• Images of happy lifestyle types retirees, young families and mid-aged
tradesmen and professionals

```html
<!DOCTYPE html>
<html lang="en">
<head>
<meta charset="utf-8">
<title>Solstice Advisory – Letterhead</title>
<link href="https://fonts.googleapis.com/css2?family=Open+Sans:wght@400;600;700&family=Oswald:wght@400&family=Roboto+Condensed:wght@400;700&display=swap" rel="stylesheet">
<style>
  :root{
    --orange:#e8601c;
    --amber:#f2b233;
    --ink:#1c1c1c;
    --paper:#ffffff;
    --photo-warm:#c9a37e;
    --photo-cool:#8c97a6;
    --signature-tone:#f4f1ee;
  }
  *{margin:0;padding:0;box-sizing:border-box}
  html,body{width:723px;height:1200px;overflow:hidden;background:var(--paper)}
  body{font-family:"Open Sans",Arial,sans-serif;color:var(--ink)}
  .letterhead{position:relative;width:723px;height:1200px;overflow:hidden;background:var(--paper)}
  .backdrop,.photo{position:absolute;left:0;top:0}
  .brand{position:absolute;left:34px;top:30px}
  .brand-mark{width:64px;height:64px;border-radius:50%;background:var(--orange);margin-left:74px;margin-bottom:14px}
  .brand-name{font-size:25px;font-weight:400;color:var(--orange);letter-spacing:-0.5px;line-height:1}
  .brand-tagline{font-size:17px;color:var(--ink);line-height:1.2;letter-spacing:-0.4px}
  .date{position:absolute;left:34px;top:216px;font-family:"Oswald",Arial,sans-serif;font-size:43px;color:#fff;letter-spacing:0.5px;line-height:1}
  .salutation{position:absolute;left:34px;top:362px;font-size:24px;line-height:1.35}
  .salutation strong{font-weight:700}
  .subject{position:absolute;left:34px;top:470px;font-size:23px;font-weight:700}
  .body-copy{position:absolute;left:36px;top:522px;width:658px;font-size:11.3px;line-height:19px;letter-spacing:-0.1px;text-align:justify}
  .body-copy p{margin-bottom:12px}
  .sign-off{position:absolute;left:34px;top:905px;font-size:19px;font-weight:600;line-height:1.2}
  .signature{position:absolute;left:34px;top:952px}
  .credential{position:absolute;left:34px;top:1080px;font-size:19px;font-weight:600;line-height:1.2}
  .signatory{position:absolute;right:33px;top:900px;width:230px}
  .signatory-name{font-size:30px;font-weight:700;line-height:1.15;white-space:nowrap;text-align:right}
  .signatory-role{font-size:20px;line-height:1.3}
  .signatory-rule{height:2px;background:var(--orange);margin:6px 0 10px}
  .signatory-location{font-family:"Roboto Condensed",Arial,sans-serif;font-size:11px;line-height:14px}
  .contact{position:absolute;right:33px;top:1084px;text-align:right;color:#fff;font-size:16px;line-height:27px}
</style>
</head>
<body>
<main class="letterhead">

  <svg class="backdrop" width="723" height="1200" viewBox="0 0 723 1200" aria-hidden="true">
    <path d="M0 191 H420 V330 C300 268 130 262 0 298 Z" fill="var(--orange)"/>
    <path d="M0 345 C130 285 300 282 430 372 L440 338 C320 262 130 258 0 318 Z" fill="var(--amber)"/>
    <path d="M0 318 C130 258 320 262 440 338 L420 300 C300 240 120 250 0 300 Z" fill="var(--orange)"/>
    <ellipse cx="560" cy="203" rx="188" ry="212" fill="none" stroke="var(--amber)" stroke-width="26"/>
    <path d="M405 80 C470 -10 640 -20 723 40" fill="none" stroke="var(--orange)" stroke-width="14"/>
    <path d="M410 340 C470 420 640 440 723 360" fill="none" stroke="var(--orange)" stroke-width="16"/>
    <path d="M0 1108 C250 1150 420 1050 723 1030 V1200 H0 Z" fill="var(--orange)"/>
    <path d="M0 1108 C250 1150 420 1050 723 1030" fill="none" stroke="var(--amber)" stroke-width="4"/>
    <path d="M0 1132 C110 1185 260 1200 420 1184 C250 1194 100 1180 0 1162 Z" fill="var(--paper)"/>
  </svg>

  <svg class="photo" width="723" height="1200" viewBox="0 0 723 1200" role="img" aria-label="Photograph of a happy young family sharing a laptop on a sofa">
    <defs>
      <radialGradient id="photoTone" cx="0.5" cy="0.45" r="0.6">
        <stop offset="0" stop-color="var(--photo-warm)"/>
        <stop offset="1" stop-color="var(--photo-cool)"/>
      </radialGradient>
    </defs>
    <ellipse cx="560" cy="203" rx="168" ry="192" fill="url(#photoTone)"/>
  </svg>

  <header class="brand">
    <div class="brand-mark"></div>
    <div class="brand-name">SOLSTICE ADVISORY</div>
    <div class="brand-tagline">Clear numbers. Better decisions</div>
  </header>

  <div class="date">23 NOVEMBER 2020</div>

  <div class="salutation"><strong>Dear,</strong><br>Lorem Ipsum</div>
  <div class="subject">RE:</div>

  <section class="body-copy">
    <p>Lorem Ipsum is simply dummy text of the printing and typesetting industry. Lorem Ipsum has been the industry's standard dummy text ever since the 1500s, when an unknown printer took a galley of type and scrambled it to make a type specimen book. It has survived not only five centuries, but also the leap into electronic typesetting, remaining essentially unchanged. It was popularised in the 1960s with the release of Letraset sheets containing Lorem Ipsum passages, and more recently with desktop publishing software like Aldus PageMaker including versions of Lorem</p>
    <p>Lorem Ipsum is simply dummy text of the printing and typesetting industry. Lorem Ipsum has been the industry's standard dummy text ever since the 1500s, when an unknown printer took a galley of type and scrambled it to make a type specimen book. It has survived not only five centuries, but also the leap into electronic typesetting, remaining essentially unchanged. It was popularised in the 1960s with the release of Letraset sheets containing Lorem Ipsum passages, and more recently with desktop publishing software like Aldus PageMaker including versions of Lorem</p>
    <p>Lorem Ipsum is simply dummy text of the printing and typesetting industry. Lorem Ipsum has been the industry's standard dummy text ever since the 1500s, when an unknown printer took a galley of type and scrambled it to make a type specimen book. It has survived not only five centuries, but also the leap into electronic typesetting, remaining essentially unchanged. It was popularised in the 1960s with the release of Letraset sheets containing Lorem Ipsum passages, and more recently with desktop publishing software like Aldus PageMaker including versions of Lorem</p>
  </section>

  <div class="sign-off">Kindest Regards</div>
  <svg class="signature" width="190" height="100" viewBox="0 0 190 100" role="img" aria-label="Handwritten signature">
    <rect width="190" height="100" rx="6" fill="var(--signature-tone)"/>
  </svg>
  <div class="credential">Chartered Accountants</div>

  <section class="signatory">
    <div class="signatory-name">Martin Hale</div>
    <div class="signatory-role">CEO and Founder</div>
    <div class="signatory-rule"></div>
    <div class="signatory-location"><strong>Location:</strong> Suite 204, Level 2, 88 Harbour Road,<br>Kelso Bay NSW 2260</div>
  </section>

  <footer class="contact">
    <div>Office: 1300 456 210</div>
    <div>Mobile: 0411 58 36 70</div>
    <div>www.solsticeadvisory.com.au</div>
    <div>admin@solsticeadvisory.com.au</div>
  </footer>

</main>
</body>
</html>
```